Modern Business Card

Modern professional business card with more than just logo and demographic info. Something memorable.

We are a trendy/modern chiropractic group with an emphasis on neurology, hence the minimalist-type brain logo. We want to convey that modern and technical aspect with professionalism and the elite nature of our practice environment.

```html
<!DOCTYPE html>
<html lang="en">
<head>
<meta charset="utf-8">
<title>Keystone Spine – Business Cards</title>
<link rel="stylesheet" href="https://fonts.googleapis.com/css2?family=Quattrocento:wght@400&family=Roboto:wght@400&family=Saira+Semi+Condensed:wght@600&display=swap">
<style>
  :root {
    --backdrop: #b4b4b4;
    --card: #f1f1f1;
    --card-edge: #e4e4e4;
    --blue: #3f5f9c;
    --brown: #3d3336;
    --ink: #2b2b2b;
    --muted: #4a4a4a;
    --band-text: #e6e6ea;
  }
  * { box-sizing: border-box; margin: 0; padding: 0; }
  html, body { width: 1200px; height: 576px; overflow: hidden; }
  body {
    position: relative;
    background: var(--backdrop);
    font-family: "Quattrocento", Georgia, serif;
    color: var(--ink);
  }
  .card {
    position: absolute;
    top: 139px;
    height: 292px;
    border-radius: 10px;
    overflow: hidden;
    background: linear-gradient(180deg, #f4f4f4 0%, var(--card) 60%, var(--card-edge) 100%);
    box-shadow: 0 3px 6px rgba(0,0,0,0.25);
  }
  .card--front { left: 82px; width: 484px; }
  .card--back { left: 602px; width: 480px; }

  /* brand lockup */
  .brand { position: absolute; display: flex; align-items: center; }
  .brand__mark { background: var(--blue); flex: none; }
  .brand__name {
    font-family: "Quattrocento", Georgia, serif;
    font-weight: 400;
    color: var(--ink);
    text-transform: uppercase;
    line-height: 0.95;
  }
  .card--front .brand { left: 0; right: 0; top: 92px; justify-content: center; gap: 14px; }
  .card--front .brand__mark { width: 70px; height: 70px; }
  .card--front .brand__name { font-size: 42px; letter-spacing: 1px; }
  .card--back .brand { left: 34px; top: 106px; gap: 9px; }
  .card--back .brand__mark { width: 46px; height: 46px; }
  .card--back .brand__name { font-size: 27px; letter-spacing: 0.5px; }

  .front__web {
    position: absolute; top: 244px; left: 0; right: 0;
    display: flex; align-items: center; justify-content: center; gap: 20px;
    font-family: "Roboto", Arial, sans-serif; font-size: 13px; color: #111;
  }
  .front__web svg { display: block; }
  .front__band { position: absolute; left: 0; right: 0; bottom: 0; height: 13px; display: flex; }
  .front__band span { flex: 1; }
  .front__band .band-blue { background: var(--blue); }
  .front__band .band-brown { background: var(--brown); }

  .contact { position: absolute; left: 275px; top: 85px; }
  .contact__name {
    font-family: "Saira Semi Condensed", "Arial Narrow", sans-serif;
    font-weight: 600; font-size: 20px; color: var(--blue); line-height: 1;
  }
  .contact__role { margin-top: 6px; font-size: 12.5px; color: var(--muted); }
  .contact__list { list-style: none; margin-top: 15px; }
  .contact__list li {
    display: flex; align-items: center; gap: 9px;
    font-size: 12.5px; color: var(--muted); height: 18.5px;
  }
  .contact__list svg { width: 12px; height: 12px; fill: var(--blue); flex: none; }

  .back__band {
    position: absolute; left: 0; right: 0; bottom: 0; height: 36px;
    background: linear-gradient(90deg, var(--brown) 0%, #4a4a66 45%, var(--blue) 100%);
    display: flex; align-items: center; justify-content: center;
    font-size: 12.5px; color: var(--band-text); letter-spacing: 0.3px;
  }
</style>
</head>
<body>

<section class="card card--front" aria-label="Business card front">
  <div class="brand">
    <span class="brand__mark"></span>
    <span class="brand__name">Keystone<br>Spine</span>
  </div>
  <div class="front__web">
    <svg width="42" height="4" viewBox="0 0 42 4"><path d="M0 2 L42 0 L42 4 Z" fill="var(--blue)"/></svg>
    <span>www.keystonespine.com</span>
    <svg width="42" height="4" viewBox="0 0 42 4"><path d="M0 0 L42 2 L0 4 Z" fill="var(--blue)"/></svg>
  </div>
  <div class="front__band"><span class="band-blue"></span><span class="band-brown"></span></div>
</section>

<section class="card card--back" aria-label="Business card back">
  <div class="brand">
    <span class="brand__mark"></span>
    <span class="brand__name">Keystone<br>Spine</span>
  </div>
  <div class="contact">
    <p class="contact__name">Daniel Reyes Ortiz</p>
    <p class="contact__role">Managing Director</p>
    <ul class="contact__list">
      <li>
        <svg viewBox="0 0 24 24"><path d="M3 8c0-3 4-5 9-5s9 2 9 5v2h-5V8H8v2H3zM6 12h12l3 9H3z"/></svg>
        555-201-4477
      </li>
      <li>
        <svg viewBox="0 0 24 24"><path d="M2 5h20v14H2z M4 7v1l8 5 8-5V7l-8 5z" fill-rule="evenodd"/></svg>
        daniel@keystonespine.com
      </li>
      <li>
        <svg viewBox="0 0 24 24"><path d="M12 2a10 10 0 1 0 0 20 10 10 0 0 0 0-20zm0 2c1.5 1.8 2.4 4.7 2.5 7h-5c.1-2.3 1-5.2 2.5-7zM4.1 11a8 8 0 0 1 4.6-6.3C7.9 6.5 7.6 8.8 7.5 11zm0 2h3.4c.1 2.2.4 4.5 1.2 6.3A8 8 0 0 1 4.1 13zm5.4 0h5c-.1 2.3-1 5.2-2.5 7-1.5-1.8-2.4-4.7-2.5-7zm7 0h3.4a8 8 0 0 1-4.6 6.3c.8-1.8 1.1-4.1 1.2-6.3zm0-2c-.1-2.2-.4-4.5-1.2-6.3a8 8 0 0 1 4.6 6.3z"/></svg>
        www.keystonespine.com
      </li>
    </ul>
  </div>
  <div class="back__band">418 Meridian Ave., Lakeview, Northfield, US 204518</div>
</section>

</body>
</html>
```